Sunflower oil

Label size 198 mm x 450 mm
Brand - VÄL
Pictorial - Sunflower swish
Text - Premium Sunflower Oil
Background colors light pastels preferred pistachio green
After initial rendition selected will add required additional text as shown on sample labels in appropriate languages

Target Market(s)

Retail / Foodservice

Industry/Entity Type

Food

Requirements
Should not have
• Black / brown / dark colors

```html
<!DOCTYPE html>
<html lang="en">
<head>
<meta charset="utf-8">
<title>VÄL Premium Sunflower Oil – Label</title>
<link rel="stylesheet" href="https://fonts.googleapis.com/css2?family=Playfair+Display:wght@900&family=Oswald:wght@700&display=swap">
<style>
  :root {
    --backdrop: #e2e2e2;
    --label-white: #f3f3f1;
    --pistachio: #4f9a5c;
    --pistachio-light: #6fb37a;
    --ribbon-green: #2f6e3d;
    --ribbon-edge: #9bcf8f;
    --gold: #d8a62a;
    --gold-light: #f2cf5b;
    --petal: #f6c21c;
    --petal-deep: #e79a0f;
    --ink-light: #ffffff;
  }
  html, body {
    margin: 0;
    padding: 0;
    width: 1200px;
    height: 960px;
    overflow: hidden;
    background: var(--backdrop);
  }
  .canvas {
    position: relative;
    width: 1200px;
    height: 960px;
  }
  .label {
    position: absolute;
    left: 80px;
    top: 251px;
    width: 1040px;
    height: 458px;
    box-shadow: 0 14px 40px rgba(0,0,0,0.12);
  }
  .label svg { display: block; }
  .brand-name {
    font-family: "Oswald", "Arial Narrow", sans-serif;
    font-weight: 700;
    font-size: 70px;
    letter-spacing: 10px;
    fill: var(--ribbon-green);
  }
  .premium-tag {
    font-family: "Playfair Display", Georgia, serif;
    font-weight: 900;
    font-size: 17px;
    letter-spacing: 1px;
    fill: var(--ribbon-green);
  }
  .product-name {
    font-family: "Oswald", "Arial Narrow", sans-serif;
    font-weight: 700;
    font-size: 48px;
    letter-spacing: 1px;
    fill: var(--ink-light);
  }
</style>
</head>
<body>
<main class="canvas">
  <section class="label" aria-label="VÄL Premium Sunflower Oil bottle label">
    <svg width="1040" height="458" viewBox="0 0 1040 458" xmlns="http://www.w3.org/2000/svg">
      <defs>
        <linearGradient id="field-green" x1="0" y1="0" x2="0" y2="1">
          <stop offset="0" stop-color="var(--pistachio-light)"/>
          <stop offset="1" stop-color="var(--pistachio)"/>
        </linearGradient>
        <radialGradient id="flower-tones" cx="0.5" cy="0.5" r="0.5">
          <stop offset="0" stop-color="#b5621d"/>
          <stop offset="0.32" stop-color="var(--petal-deep)"/>
          <stop offset="0.55" stop-color="var(--petal)"/>
          <stop offset="1" stop-color="var(--gold-light)"/>
        </radialGradient>
      </defs>

      <rect class="label-base" width="1040" height="458" fill="var(--label-white)"/>

      <path class="green-field" d="M0 110 C 200 150, 360 250, 520 250 C 690 250, 850 170, 1040 120 L 1040 458 L 0 458 Z" fill="url(#field-green)"/>
      <path class="gold-swish" d="M0 96 C 200 136, 360 236, 520 236 C 690 236, 850 156, 1040 106" fill="none" stroke="var(--gold)" stroke-width="9"/>
      <path class="gold-swish-fine" d="M0 112 C 200 152, 360 252, 520 252 C 690 252, 850 172, 1040 122" fill="none" stroke="var(--gold-light)" stroke-width="3"/>

      <text class="brand-name" x="525" y="122" text-anchor="middle">VÄL</text>

      <circle class="sunflower-art" cx="520" cy="270" r="118" fill="url(#flower-tones)" role="img" aria-label="Sunflower illustration with golden petals"/>

      <g class="premium-ribbon" transform="rotate(-8 520 316)">
        <rect x="455" y="302" width="130" height="26" fill="var(--gold-light)"/>
        <text class="premium-tag" x="520" y="322" text-anchor="middle">PREMIUM</text>
      </g>

      <g class="product-ribbon" transform="rotate(-8 520 382)">
        <path d="M300 352 L340 352 L340 412 L300 412 L316 382 Z" fill="var(--ribbon-green)" opacity="0.8"/>
        <path d="M740 352 L700 352 L700 412 L740 412 L724 382 Z" fill="var(--ribbon-green)" opacity="0.8"/>
        <rect x="330" y="346" width="380" height="72" fill="var(--ribbon-green)" stroke="var(--ribbon-edge)" stroke-width="3"/>
        <text class="product-name" x="520" y="401" text-anchor="middle">SUNFLOWER OIL</text>
      </g>
    </svg>
  </section>
</main>
</body>
</html>
```